Business Card Design Project

Business card based on attached logo

Todd Merrick
Todd@lorvantest.com
877-514-9073 ext. 318
Www.LorvanTest.com

Industry/Entity Type

Business

```html
<!DOCTYPE html>
<html lang="en">
<head>
<meta charset="utf-8">
<title>LorvanTest Business Card</title>
<link href="https://fonts.googleapis.com/css2?family=Roboto:wght@300;400;700;900&display=swap" rel="stylesheet">
<style>
  :root {
    --backdrop: #8a8c8f;
    --paper-light: #f4f4f4;
    --paper-shade: #dcdcdc;
    --brand-red: #e0262b;
    --brand-red-deep: #c81f26;
    --ink: #231f20;
    --charcoal: #1f1f1f;
    --charcoal-glow: #3a3a3a;
    --white: #ffffff;
  }
  * { box-sizing: border-box; margin: 0; padding: 0; }
  html, body {
    width: 1200px; height: 720px; overflow: hidden;
    background: var(--backdrop);
    font-family: "Roboto", Arial, sans-serif;
  }
  .sheet { position: relative; width: 1200px; height: 720px; }
  .card { position: absolute; width: 565px; height: 323px; overflow: hidden; }
  .card--front   { left: 24px;  top: 26px;  background: linear-gradient(90deg, var(--paper-light), #fafafa 60%, var(--paper-shade)); border: 1px solid #6f6f6f; }
  .card--red     { left: 612px; top: 26px;  background: linear-gradient(120deg, var(--brand-red) 0%, var(--brand-red-deep) 100%); }
  .card--mark    { left: 24px;  top: 374px; background: linear-gradient(90deg, var(--paper-light), #fafafa 55%, var(--paper-shade)); }
  .card--dark    { left: 612px; top: 374px; background: radial-gradient(ellipse at 45% 40%, var(--charcoal-glow), var(--charcoal) 70%); }

  .brand-name { font-weight: 900; letter-spacing: -1px; line-height: 1; white-space: nowrap; }

  /* front */
  .front-brand { position: absolute; left: 30px; top: 138px; font-size: 44px; color: var(--ink); }
  .front-divider { position: absolute; left: 296px; top: 85px; width: 2px; height: 138px; background: #c9c9c9; }
  .holder { position: absolute; left: 320px; top: 115px; }
  .holder-name { color: var(--brand-red); font-size: 19px; font-weight: 400; text-transform: uppercase; margin-bottom: 18px; }
  .contact-line { display: flex; align-items: center; gap: 7px; font-size: 17px; color: var(--ink); margin-bottom: 7px; }
  .contact-line svg { width: 14px; height: 14px; flex: none; }
  .front-rule { position: absolute; left: 0; right: 0; top: 281px; height: 2px; background: var(--brand-red); }
  .front-footer { position: absolute; left: 0; right: 0; top: 286px; bottom: 0; background: var(--charcoal); }

  .web { position: absolute; font-size: 16px; letter-spacing: 2.6px; font-weight: 400; }
  .front-footer .web { left: 158px; top: 10px; color: var(--white); }

  /* red */
  .red-brand { position: absolute; left: 34px; top: 52px; font-size: 78px; color: var(--white); }
  .red-square { position: absolute; right: 0; top: 152px; width: 170px; height: 170px; background: rgba(255,255,255,0.12); }
  .card--red .web { left: 36px; top: 292px; color: var(--white); }

  /* mark */
  .mark-square { position: absolute; left: 218px; top: 84px; width: 130px; height: 130px; background: var(--brand-red); }
  .card--mark .web { left: 158px; top: 280px; color: var(--ink); }

  /* dark */
  .dark-brand { position: absolute; left: 0; right: 0; top: 108px; text-align: center; font-size: 76px; color: var(--white); }
  .card--dark .web { left: 0; right: 0; top: 280px; text-align: center; color: var(--white); }
</style>
</head>
<body>
<main class="sheet">

  <section class="card card--front" aria-label="Card front">
    <div class="brand-name front-brand">LorvanTest</div>
    <div class="front-divider"></div>
    <div class="holder">
      <p class="holder-name">Todd Merrick</p>
      <p class="contact-line">
        <svg viewBox="0 0 16 16" aria-hidden="true"><circle cx="8" cy="8" r="7.2" fill="none" stroke="#e0262b" stroke-width="1.4"/><path d="M5.2 4.3l1.6-.3.8 2-1 .8c.5 1.2 1.3 2 2.5 2.5l.8-1 2 .8-.3 1.6c-3.4.3-6.7-3-6.4-6.4z" fill="#e0262b"/></svg>
        877-514-9073 ext. 318
      </p>
      <p class="contact-line">
        <svg viewBox="0 0 16 16" aria-hidden="true"><path d="M1.5 6.5L8 2l6.5 4.5V13h-13z" fill="#e0262b"/><path d="M1.5 6.5L8 10.5l6.5-4" fill="none" stroke="#fff" stroke-width="1.2"/></svg>
        Todd@lorvantest.com
      </p>
    </div>
    <div class="front-rule"></div>
    <div class="front-footer"><span class="web">www.lorvantest.com</span></div>
  </section>

  <section class="card card--red" aria-label="Card back, red">
    <div class="brand-name red-brand">LorvanTest</div>
    <div class="red-square"></div>
    <span class="web">www.lorvantest.com</span>
  </section>

  <section class="card card--mark" aria-label="Card back, light">
    <div class="mark-square"></div>
    <span class="web">www.lorvantest.com</span>
  </section>

  <section class="card card--dark" aria-label="Card back, dark">
    <div class="brand-name dark-brand">LorvanTest</div>
    <span class="web">www.lorvantest.com</span>
  </section>

</main>
</body>
</html>
```